Outdoor Real Estate Sales Banner

It should say

248 Wexcombe Street, East Boston
Coming Spring 2026
3 Luxury Condos
Experience refined living with elegant design and high-end finishes. Thoughtfully crafted for both comfort and sophistication.
Construction by V Construction
Now Accepting Reservations

Schedule Your Private Tour Today
Marisol Thibault, Fenwick Realty | 617-555-0142 | Marisol@fenwickharbor.com
Gregory Hale, Fenwick Realty | 617-555-0187 | Gregory@fenwickharbor.com

Target Market(s)

30-45

Industry/Entity Type

real estate

Font styles to use
Serif

Requirements
Must have
• Colors of logo and preppy rich look
Nice to have
• herringbone incorporated the pattern
Should not have
• any loud colors

```html
<!DOCTYPE html>
<html lang="en">
<head>
<meta charset="utf-8">
<title>Fenwick Realty – Coming Spring 2026</title>
<link rel="stylesheet" href="https://fonts.googleapis.com/css2?family=Playfair+Display:ital,wght@0,400;0,500;1,600;1,700&display=swap">
<style>
  :root {
    --page: #e4e4e4;
    --navy-deep: #0f1f4d;
    --navy: #1a2f6e;
    --navy-light: #24408a;
    --gold: #e6b661;
    --gold-soft: #c9a35a;
    --white: #ffffff;
    --serif: "Playfair Display", Georgia, serif;
  }
  * { box-sizing: border-box; margin: 0; padding: 0; }
  html, body { width: 1200px; height: 696px; overflow: hidden; background: var(--page); }
  .banner {
    position: absolute; left: 20px; top: 58px; width: 1160px; height: 580px;
    overflow: hidden; font-family: var(--serif); color: var(--white);
  }
  .backdrop {
    position: absolute; inset: 0;
    background:
      radial-gradient(ellipse at 78% 65%, rgba(60,90,160,.45), transparent 60%),
      radial-gradient(ellipse at 35% 35%, rgba(50,75,140,.35), transparent 55%),
      linear-gradient(180deg, var(--navy-light) 0%, var(--navy) 45%, var(--navy-deep) 100%);
  }
  .house-photo {
    position: absolute; left: 0; top: 68px; width: 255px; height: 300px;
    background: linear-gradient(180deg, #e9e7e2 0%, #cfc6b6 40%, #b8925c 70%, #2f3140 100%);
  }
  .brand { position: absolute; left: 380px; top: 50px; width: 400px; text-align: center; }
  .brand-mark {
    display: block; width: 76px; height: 76px; margin: 0 auto 10px;
    border: 2px solid var(--gold); border-radius: 50%;
  }
  .brand-name { color: var(--gold); font-size: 24px; font-weight: 400; letter-spacing: 2px; }
  .address {
    position: absolute; left: 180px; top: 214px; width: 800px; text-align: center;
    font-size: 29px; font-weight: 500; letter-spacing: -.5px;
  }
  .address .sep { color: var(--gold); margin: 0 4px; font-weight: 400; }
  .headline {
    position: absolute; left: 180px; top: 260px; width: 800px; text-align: center;
    color: var(--gold); font-size: 66px; font-style: italic; font-weight: 700; letter-spacing: -2px;
  }
  .subhead {
    position: absolute; left: 180px; top: 364px; width: 800px; text-align: center;
    color: var(--gold); font-size: 32px; font-weight: 400; letter-spacing: -.5px;
  }
  .description {
    position: absolute; left: 230px; top: 420px; width: 700px; text-align: center;
    font-size: 18px; line-height: 23px; letter-spacing: -.3px;
  }
  .builder {
    position: absolute; left: 378px; top: 510px; width: 405px;
    display: flex; align-items: center; gap: 10px; color: var(--gold); font-size: 19px; white-space: nowrap;
  }
  .builder .rule { flex: 1; height: 1px; background: var(--gold-soft); opacity: .7; }
  .reservation-tag {
    position: absolute; left: 42px; top: 413px; padding: 5px 10px 6px;
    background: var(--gold); color: var(--navy-deep); font-size: 21px; letter-spacing: -.4px;
    transform: rotate(-2.5deg); transform-origin: left center; white-space: nowrap;
  }
  .tour-cta {
    position: absolute; left: 50px; top: 456px; font-size: 31px; line-height: 38px;
    font-weight: 500; letter-spacing: -1px;
  }
  .agents { position: absolute; left: 887px; top: 378px; width: 250px; }
  .agent-name { color: var(--gold); font-size: 18px; letter-spacing: -.3px; margin-bottom: 2px; }
  .agent-line { display: flex; align-items: center; gap: 9px; font-size: 15px; line-height: 21px; letter-spacing: -.3px; }
  .agent-line svg { width: 12px; height: 12px; fill: var(--gold); flex: none; }
  .agent-divider { height: 1px; background: var(--gold-soft); opacity: .6; margin: 11px 0 10px; width: 200px; }
</style>
</head>
<body>
<main class="banner">
  <div class="backdrop" role="img" aria-label="Night view of modern luxury residences beside a lit pool, tinted deep navy"></div>

  <div class="house-photo" role="img" aria-label="Modern three-storey white luxury home with glass walls and warm interior lights"></div>

  <header class="brand">
    <span class="brand-mark"></span>
    <div class="brand-name">FENWICK REALTY</div>
  </header>

  <p class="address">248 Wexcombe Street<span class="sep">|</span>East Boston</p>
  <h1 class="headline">Coming Spring 2026</h1>
  <h2 class="subhead">3 Exclusive Luxury Residences</h2>
  <p class="description">Refined living featuring elegant design and premium<br>finishes, crafted for comfort &amp; sophistication.</p>
  <p class="builder"><span class="rule"></span>Built by V Construction<span class="rule"></span></p>

  <p class="reservation-tag">Reservations Now Open</p>
  <p class="tour-cta">Schedule Your<br>Private Tour Today</p>

  <section class="agents">
    <div class="agent">
      <p class="agent-name">Marisol Thibault</p>
      <p class="agent-line"><svg viewBox="0 0 24 24"><path d="M6.6 10.8a15.1 15.1 0 0 0 6.6 6.6l2.2-2.2c.3-.3.7-.4 1-.2 1.1.4 2.3.6 3.6.6.6 0 1 .4 1 1V20c0 .6-.4 1-1 1A17 17 0 0 1 3 4c0-.6.4-1 1-1h3.5c.6 0 1 .4 1 1 0 1.3.2 2.5.6 3.6.1.3 0 .7-.2 1z"/></svg>617-555-0142</p>
      <p class="agent-line"><svg viewBox="0 0 24 24"><path d="M2 5h20v2l-10 6L2 7z M2 9l10 6 10-6v10H2z"/></svg>marisol@fenwickharbor.com</p>
    </div>
    <div class="agent-divider"></div>
    <div class="agent">
      <p class="agent-name">Gregory Hale</p>
      <p class="agent-line"><svg viewBox="0 0 24 24"><path d="M6.6 10.8a15.1 15.1 0 0 0 6.6 6.6l2.2-2.2c.3-.3.7-.4 1-.2 1.1.4 2.3.6 3.6.6.6 0 1 .4 1 1V20c0 .6-.4 1-1 1A17 17 0 0 1 3 4c0-.6.4-1 1-1h3.5c.6 0 1 .4 1 1 0 1.3.2 2.5.6 3.6.1.3 0 .7-.2 1z"/></svg>617-555-0187</p>
      <p class="agent-line"><svg viewBox="0 0 24 24"><path d="M2 5h20v2l-10 6L2 7z M2 9l10 6 10-6v10H2z"/></svg>gregory@fenwickharbor.com</p>
    </div>
  </section>
</main>
</body>
</html>
```